Business Card and Letterhead for Pimlu - modern real estate business

I need a double sided business card design for Pimlu. Please see business card brief here https://files.trelvonadocs.com/sheet/r/7QzTmWbaXLJnoPEd-kRyUgFhHsstbvCe2qfoMxDa_pz/view?mode=shared

Please feel free to design the business cards however you feel best. I am happy to give some creative freedoms and then provide feedback from there.

Please then also create a letterhead to match the business card design

Colors

Designer to choose colors to be used in the design.

Requirements
Must have
• Must be a modern, elegant business card which looks very professional

```html
<!DOCTYPE html>
<html lang="en">
<head>
<meta charset="utf-8">
<title>Pimlu – Business Card</title>
<link href="https://fonts.googleapis.com/css2?family=Poppins:wght@400;600&display=swap" rel="stylesheet">
<style>
  :root {
    --page: #e9e7e4;
    --black: #000000;
    --white: #ffffff;
    --brand-red: #e3202a;
    --ink: #1a1a1a;
    --photo-dark: #3b4a3a;
    --photo-light: #a8b59a;
  }
  html, body {
    margin: 0;
    padding: 0;
    width: 1200px;
    height: 800px;
    overflow: hidden;
    background: var(--page);
    font-family: "Poppins", sans-serif;
  }
  .canvas {
    position: relative;
    width: 1200px;
    height: 800px;
  }
  .card {
    position: absolute;
    width: 584px;
    height: 360px;
    overflow: hidden;
    box-shadow: 0 4px 14px rgba(0, 0, 0, 0.25);
  }
  .card-back {
    left: 82px;
    top: 35px;
    background: var(--black);
  }
  .card-back .brand-name {
    position: absolute;
    left: 0;
    right: 0;
    top: 141px;
    text-align: center;
    font-size: 74px;
    font-weight: 600;
    letter-spacing: 16px;
    text-indent: 16px;
    color: var(--brand-red);
    line-height: 1;
  }
  .card-front {
    left: 522px;
    top: 409px;
    background: var(--white);
  }
  .front-band {
    position: absolute;
    left: 0;
    top: 0;
    width: 230px;
    height: 360px;
    background: var(--black);
  }
  .portrait {
    position: absolute;
    left: 30px;
    top: 37px;
    width: 222px;
    height: 222px;
  }
  .card-front .brand-name {
    position: absolute;
    left: 283px;
    top: 50px;
    font-size: 52px;
    font-weight: 600;
    letter-spacing: 12px;
    color: var(--brand-red);
    line-height: 1;
  }
  .agent-name {
    position: absolute;
    left: 288px;
    top: 162px;
    margin: 0;
    font-size: 21px;
    font-weight: 600;
    color: var(--ink);
  }
  .agent-role {
    position: absolute;
    left: 288px;
    top: 192px;
    margin: 0;
    font-size: 13.5px;
    color: var(--ink);
  }
  .postal {
    position: absolute;
    left: 288px;
    top: 231px;
    margin: 0;
    font-size: 12.5px;
    line-height: 18px;
    color: var(--ink);
    font-style: normal;
  }
  .contact-list {
    position: absolute;
    top: 285px;
    margin: 0;
    padding: 0;
    list-style: none;
    font-size: 12.5px;
    line-height: 18px;
    color: var(--ink);
    white-space: nowrap;
  }
  .contact-list li {
    display: flex;
    align-items: center;
    gap: 6px;
  }
  .contact-phones { left: 292px; }
  .contact-online { left: 428px; }
  .icon { width: 10px; height: 10px; flex: none; }
  .icon-fill { fill: var(--ink); }
  .icon-line { fill: none; stroke: var(--ink); }
</style>
</head>
<body>
<div class="canvas">

  <section class="card card-back" aria-label="Business card back">
    <div class="brand-name">PIMLU</div>
  </section>

  <section class="card card-front" aria-label="Business card front">
    <div class="front-band"></div>

    <svg class="portrait" viewBox="0 0 222 222" role="img" aria-label="Portrait photo of the agent in a dark suit, outdoors with trees and hills behind">
      <defs>
        <linearGradient id="portraitTone" x1="0" y1="0" x2="1" y2="1">
          <stop offset="0" stop-color="#a8b59a"/>
          <stop offset="1" stop-color="#3b4a3a"/>
        </linearGradient>
      </defs>
      <circle cx="111" cy="111" r="111" fill="#ffffff"/>
      <circle cx="111" cy="111" r="100" fill="url(#portraitTone)"/>
    </svg>

    <div class="brand-name">PIMLU</div>

    <h1 class="agent-name">Dane Marlow</h1>
    <p class="agent-role">Licenced Real Estate Agent</p>

    <address class="postal">PO Box 5120<br>Tarrowby NSW 2790</address>

    <ul class="contact-list contact-phones">
      <li><svg class="icon icon-fill" viewBox="0 0 10 10"><path d="M1 3.5C1 2 2.5 1.5 5 1.5S9 2 9 3.5L7.5 4 7 3H3L2.5 4Z M2.5 5h5l1 3.5h-7Z"/></svg>0412 386 904</li>
      <li><svg class="icon icon-fill" viewBox="0 0 10 10"><path d="M1 3.5C1 2 2.5 1.5 5 1.5S9 2 9 3.5L7.5 4 7 3H3L2.5 4Z M2.5 5h5l1 3.5h-7Z"/></svg>1300 547 218</li>
    </ul>

    <ul class="contact-list contact-online">
      <li><svg class="icon" viewBox="0 0 10 10"><rect class="icon-fill" x="0.5" y="2" width="9" height="6"/><path d="M0.8 2.3 5 5.4 9.2 2.3" fill="none" stroke="#ffffff" stroke-width="0.8"/></svg>dane@pimlu.com</li>
      <li><svg class="icon" viewBox="0 0 10 10"><circle class="icon-line" cx="5" cy="5" r="4.3" stroke-width="1"/><ellipse class="icon-line" cx="5" cy="5" rx="1.8" ry="4.3" stroke-width="0.8"/><path class="icon-line" d="M0.8 5h8.4" stroke-width="0.8"/></svg>www.pimlu.com</li>
    </ul>
  </section>

</div>
</body>
</html>
```